Life Coaching business needs a new flyer

We are an Australian business that specialises in Life Coaching, Career Coaching, Health and Wellness Coaching, Yoga and Pilates. We need a A4 double sided flyer that is full colour and folded to DL format. I have attached a couple of designs that I like and some pictures and would like the flyer to be bright yet stylish.

Industry/Entity Type

Life Coaching

```html
<!DOCTYPE html>
<html lang="en">
<head>
<meta charset="utf-8">
<title>Brightpath Coaching Flyer</title>
<link href="https://fonts.googleapis.com/css2?family=Roboto+Slab:wght@300;400&display=swap" rel="stylesheet">
<style>
:root{
  --blue:#2b96d1;
  --green:#5cb646;
  --ink:#3a3a3a;
  --white:#ffffff;
  --page:#eeeeee;
  --photo-warm:#d9a77e;
  --photo-sky:#8ec8ea;
}
*{box-sizing:border-box;margin:0;padding:0}
html,body{width:858px;height:1200px;overflow:hidden}
body{background:var(--page);font-family:"Roboto Slab",serif;font-weight:300;color:var(--ink);position:relative}
.sheet{position:absolute;left:21px;width:816px;height:578px;overflow:hidden;background:var(--white);box-shadow:0 0 3px rgba(0,0,0,.25)}
.sheet--outside{top:18px}
.sheet--inside{top:606px}
.abs{position:absolute}
.panel{position:absolute;top:0;height:578px;width:272px}
.panel--blue{background:var(--blue);color:var(--white)}
.panel--white{background:var(--white)}
.body-text{font-size:9.4px;line-height:15.2px}

/* testimonials */
.band{position:absolute;display:flex;align-items:center;font-weight:400}
.band--green{background:var(--green);color:var(--white)}
.band--white{background:var(--white);color:var(--green)}
.clients-title{top:30px;left:0;width:250px;height:32px;justify-content:center;font-size:19px;letter-spacing:.3px}
.quote{position:absolute;left:16px;width:242px;border:2px solid var(--blue);border-left-width:2px;border-radius:3px;padding:10px 12px 6px 30px;font-size:8px;line-height:12.8px;color:#2f6fa3}
.quote::before,.quote::after{position:absolute;color:var(--green);font-size:34px;font-weight:400;line-height:1}
.quote::before{content:"\201C";left:-2px;top:4px;background:var(--white);padding:0 2px}
.quote::after{content:"\201D";right:-6px;bottom:-18px;background:var(--white);padding:0 2px}
.quote-name{color:var(--green);font-size:11.5px;margin-top:4px;font-weight:400}
.social{top:546px;left:20px;display:flex;gap:14px;align-items:center;font-size:11.5px;color:var(--ink);font-weight:400}
.social-item{display:flex;align-items:center;gap:6px}
.dot{width:20px;height:20px;border-radius:50%;background:var(--green);display:inline-block}

/* photos */
.photo{position:absolute;border-radius:50%;border:5px solid var(--white);box-shadow:0 0 0 2px var(--green)}
.photo--woman{left:276px;top:228px;width:260px;height:260px;background:radial-gradient(circle at 50% 40%,#f4c9b0,#e07a9a 55%,#7fc0e6)}
.photo--group{left:494px;top:122px;width:344px;height:344px;background:radial-gradient(circle at 40% 45%,var(--photo-warm),#b06a4e 55%,var(--photo-sky))}
.thumb{position:absolute;width:60px;height:60px;border-radius:50%;border:3px solid var(--white);box-shadow:0 0 0 2px var(--green),2px 2px 4px rgba(0,0,0,.25)}
.thumb--signs{background:radial-gradient(circle,#7fb6dc,#2d5f8a)}
.thumb--meditate{background:radial-gradient(circle,#e8e4ef,#8fb3d8)}
.thumb--yoga{background:linear-gradient(#9fd3f0,#f2f6fa)}
.thumb-label{position:absolute;width:70px;text-align:center;font-size:8.6px;line-height:10px;color:var(--white);font-weight:400}

/* front text */
.centre-title{left:298px;top:30px;width:230px;font-size:19.5px;line-height:24px;font-weight:400;color:var(--white)}
.centre-intro{left:298px;top:114px;width:222px}
.contact{left:290px;font-size:11.5px;color:var(--white);display:flex;align-items:center;gap:10px;font-weight:400}
.contact svg{width:12px;height:12px}
.brand-box{left:544px;top:0;width:272px;height:78px;background:var(--white);border-bottom-left-radius:22px;display:flex;align-items:center;gap:8px;padding-left:28px}
.brand-mark{width:30px;height:30px;border-radius:50%;background:var(--green)}
.brand-name{font-size:13.5px;line-height:16px;color:var(--blue);font-weight:400}
.website{left:544px;width:272px;top:546px;text-align:center;font-size:11.5px;color:var(--white);font-weight:400}

/* inside */
.questions{left:22px;top:30px;width:240px;list-style:none;font-size:9.4px;line-height:14.6px;color:var(--white)}
.questions li{position:relative;padding-left:20px;margin-bottom:0}
.questions li::before{content:"";position:absolute;left:0;top:2px;width:10px;height:10px;border-radius:50%;background:var(--white)}
.questions li::after{content:"";position:absolute;left:2.5px;top:5px;width:3px;height:3px;border-right:1.5px solid var(--blue);border-bottom:1.5px solid var(--blue);transform:rotate(-45deg)}
.mission-title{top:151px;left:0;width:272px;height:32px;padding-left:22px;font-size:14.5px}
.mission-text{left:22px;width:240px;color:var(--white)}
.photo--answer{left:-54px;top:354px;width:368px;height:368px;background:radial-gradient(circle at 45% 70%,#e8a48a,#c8564a 40%,#5aa6d8 75%)}
.answer-line{left:0;width:240px;top:400px;text-align:center;font-size:18px;line-height:23px;color:var(--white);font-weight:400}
.section-mark{width:64px;height:64px}
.lc-title{top:46px;left:362px;width:180px;height:32px;padding-left:44px;font-size:14.5px}
.col-text{left:310px;width:228px;color:var(--white)}
.col-head{left:310px;font-size:12px;color:var(--white);font-weight:400}
.why-head{left:582px;top:34px;font-size:11.5px;color:var(--green);font-weight:400}
.why-text{left:582px;width:220px;color:var(--ink)}
.why-sub{left:582px;top:101px;font-size:10px;color:var(--green);font-weight:400}
.ticks{left:582px;top:126px;list-style:none;font-size:9.4px;line-height:15.2px;color:var(--ink)}
.ticks li{display:flex;align-items:center;gap:8px}
.ticks svg{width:10px;height:10px;flex:none}
.side-title{left:634px;width:182px;height:32px;padding-left:46px;font-size:14.5px}
.side-text{left:580px;width:230px;color:var(--ink)}
</style>
</head>
<body>

<!-- Outside of the folded sheet -->
<section class="sheet sheet--outside">
  <div class="panel panel--white" style="left:0">
    <h2 class="band band--green clients-title">OUR HAPPY CLIENTS</h2>

    <blockquote class="quote" style="top:78px;height:100px">
      I have lost 10 kilos and now have the energy to play with my kids. Thanks Maren for you support/guidance and helping me get rid of my limiting beliefs. I feel I can achieve anything now! The sky's the limit.
      <p class="quote-name">Tessa, Mosman</p>
    </blockquote>

    <blockquote class="quote" style="top:196px;height:86px">
      Maren has helped to change my life around in all aspects. I would have been lost without her. Thanks Maren for your professionalism, support and guidance.
      <p class="quote-name">Noelle, Cremorne</p>
    </blockquote>

    <blockquote class="quote" style="top:302px;height:73px">
      I was so busy with kids, work, and my husband I lost who I was. Maren has helped me find the person I am again.
      <p class="quote-name">Greta, Chatswood</p>
    </blockquote>

    <blockquote class="quote" style="top:394px;height:128px">
      "When I started with Coach Maren, I didn't know anything about coaching. I called her because she helped a friend of mine make a career change that was a perfect fit for her. I had the opportunity to make a change too and did not know where to start. I am now in a job that I love. I would recommend Maren to everyone."
      <p class="quote-name">Declan, Texas America</p>
    </blockquote>

    <div class="abs social">
      <span class="social-item"><span class="dot"></span>@brightpathstudio</span>
      <span class="social-item"><span class="dot"></span>@brightpath</span>
    </div>
  </div>

  <div class="panel panel--blue" style="left:272px"></div>
  <div class="panel panel--blue" style="left:544px"></div>

  <div class="photo photo--group" role="img" aria-label="Photo of a group of smiling friends outdoors"></div>
  <div class="photo photo--woman" role="img" aria-label="Photo of a joyful woman with raised arms beside a pink car"></div>

  <h1 class="abs centre-title">Brightpath Coaching and Meditation Studio</h1>
  <div class="abs centre-intro body-text" style="color:var(--white)">
    <p>A professional service that can help you achieve the goals that you are looking for in Life Coaching, Meditation, and Yoga/Pilates.</p>
    <p style="margin-top:15px">If you are ready to take your life to the next level and would like to know more, please contact us.</p>
  </div>

  <div class="abs contact" style="top:524px">
    <svg viewBox="0 0 24 24"><path fill="#fff" d="M6.6 10.8c1.4 2.8 3.8 5.1 6.6 6.6l2.2-2.2c.3-.3.7-.4 1-.2 1.1.4 2.3.6 3.6.6.6 0 1 .4 1 1V20c0 .6-.4 1-1 1C10.6 21 3 13.4 3 4c0-.6.4-1 1-1h3.5c.6 0 1 .4 1 1 0 1.3.2 2.5.6 3.6.1.3 0 .7-.2 1z"/></svg>
    02 9000 4120
  </div>
  <div class="abs contact" style="top:542px">
    <svg viewBox="0 0 24 24"><rect x="2" y="5" width="20" height="14" fill="none" stroke="#fff" stroke-width="2"/><path d="M2 5l10 8 10-8" fill="none" stroke="#fff" stroke-width="2"/></svg>
    hello@brightpathstudio.com.au
  </div>

  <div class="abs brand-box">
    <span class="brand-mark"></span>
    <span class="brand-name">Brightpath Coaching<br>and Meditation Studio</span>
  </div>

  <div class="thumb thumb--signs" style="left:561px;top:437px" role="img" aria-label="Photo of a crossroads signpost"></div>
  <div class="thumb thumb--meditate" style="left:651px;top:437px" role="img" aria-label="Photo of two people meditating"></div>
  <div class="thumb thumb--yoga" style="left:740px;top:437px" role="img" aria-label="Photo of a yoga pose on the beach"></div>
  <p class="thumb-label" style="left:556px;top:508px">Life<br>Coaching</p>
  <p class="thumb-label" style="left:646px;top:513px">Meditation</p>
  <p class="thumb-label" style="left:735px;top:508px">Yoga/<br>Pilates</p>

  <p class="abs website">www.brightpathstudio.com.au</p>
</section>

<!-- Inside of the folded sheet -->
<section class="sheet sheet--inside">
  <div class="panel panel--blue" style="left:0">
    <ul class="abs questions">
      <li>Are you looking at making changes this year?</li>
      <li>Are you stuck in a rut or at a crossroad in your life?</li>
      <li>Are you wanting to lose weigh but can't get motivated?</li>
      <li>Do you have ongoing problems with your career, relationships, or just life itself?</li>
    </ul>
    <h2 class="band band--white mission-title">OUR MISSION</h2>
    <p class="abs mission-text body-text" style="top:196px">To help you become the best possible person you can be. Mentally, physically, and spiritually.</p>
    <p class="abs mission-text body-text" style="top:241px">We offer highly qualified and compassionate trainers/coaches for Life Coaching, Meditation, Yoga and Pilates.</p>
    <p class="abs mission-text body-text" style="top:301px">We will guide and motivate you every step of the way to achieve all your dreams and goals.</p>
    <div class="photo photo--answer" role="img" aria-label="Photo of cheerful young friends under a blue sky"></div>
    <p class="abs answer-line">Life coaching is<br>the answer!</p>
  </div>

  <div class="panel panel--blue" style="left:272px"></div>
  <h2 class="band band--white lc-title">LIFE COACHING</h2>
  <div class="thumb thumb--signs section-mark" style="left:300px;top:30px" role="img" aria-label="Photo of a crossroads signpost"></div>

  <p class="abs col-text body-text" style="top:118px">Your Life Coach will give you the confidence and the ability to move forward in a positive manner in all areas of your life where you crave change.</p>
  <p class="abs col-text body-text" style="top:188px">Life Coaching is about breaking down the barriers preventing this change from happening, and creating the ideal environment for positive action to take place. It is a holistic approach, which looks at the present and sets goals for a totally successful future.</p>
  <h3 class="abs col-head" style="top:286px">CAREER COACHING</h3>
  <p class="abs col-text body-text" style="top:305px">Are you at a crossroads in your career and at a loss about what to do next? Do you want your work to be in alignment with the authentic you? It can be difficult to assess career options, goals, and strategies, and have the confidence to implement changes on your own. With the right coaching support, you will gain the clarity that you need to take control and have a fulfilling and rewarding career.</p>
  <h3 class="abs col-head" style="top:453px">WELLNESS COACHING</h3>
  <p class="abs col-text body-text" style="top:472px">Health and wellness coaches help their clients find the motivation and tools to achieve their health and wellness goals, working with the client to examine and improve the psychological framework that supports those goals.</p>

  <h2 class="abs why-head">WHY WOULD I NEED HELP?</h2>
  <p class="abs why-text body-text" style="top:62px">Coaching is for anyone who wants to make lasting changes in their life.</p>
  <p class="abs why-sub">Coaching can assist with such issues as:</p>
  <ul class="abs ticks">
    <li><svg viewBox="0 0 10 10"><circle cx="5" cy="5" r="5" fill="#2b96d1"/><path d="M2.6 5.2l1.6 1.6 3.2-3.4" fill="none" stroke="#fff" stroke-width="1.3"/></svg>Creating a better work- life balance</li>
    <li><svg viewBox="0 0 10 10"><circle cx="5" cy="5" r="5" fill="#2b96d1"/><path d="M2.6 5.2l1.6 1.6 3.2-3.4" fill="none" stroke="#fff" stroke-width="1.3"/></svg>Resolving relationship issues</li>
    <li><svg viewBox="0 0 10 10"><circle cx="5" cy="5" r="5" fill="#2b96d1"/><path d="M2.6 5.2l1.6 1.6 3.2-3.4" fill="none" stroke="#fff" stroke-width="1.3"/></svg>Career guidance</li>
    <li><svg viewBox="0 0 10 10"><circle cx="5" cy="5" r="5" fill="#2b96d1"/><path d="M2.6 5.2l1.6 1.6 3.2-3.4" fill="none" stroke="#fff" stroke-width="1.3"/></svg>Stress management</li>
    <li><svg viewBox="0 0 10 10"><circle cx="5" cy="5" r="5" fill="#2b96d1"/><path d="M2.6 5.2l1.6 1.6 3.2-3.4" fill="none" stroke="#fff" stroke-width="1.3"/></svg>Weight loss and fitness</li>
    <li><svg viewBox="0 0 10 10"><circle cx="5" cy="5" r="5" fill="#2b96d1"/><path d="M2.6 5.2l1.6 1.6 3.2-3.4" fill="none" stroke="#fff" stroke-width="1.3"/></svg>Motivation and goal setting</li>
    <li><svg viewBox="0 0 10 10"><circle cx="5" cy="5" r="5" fill="#2b96d1"/><path d="M2.6 5.2l1.6 1.6 3.2-3.4" fill="none" stroke="#fff" stroke-width="1.3"/></svg>Boosting your self esteem</li>
    <li><svg viewBox="0 0 10 10"><circle cx="5" cy="5" r="5" fill="#2b96d1"/><path d="M2.6 5.2l1.6 1.6 3.2-3.4" fill="none" stroke="#fff" stroke-width="1.3"/></svg>Overcoming negative emotions and thoughts</li>
    <li><svg viewBox="0 0 10 10"><circle cx="5" cy="5" r="5" fill="#2b96d1"/><path d="M2.6 5.2l1.6 1.6 3.2-3.4" fill="none" stroke="#fff" stroke-width="1.3"/></svg>Better time management</li>
  </ul>

  <h2 class="band band--green side-title" style="top:290px">MEDITATION</h2>
  <div class="thumb thumb--meditate section-mark" style="left:566px;top:274px" role="img" aria-label="Photo of two people meditating"></div>
  <p class="abs side-text body-text" style="top:352px">We specialise in teaching meditation from beginners to advanced and teach a variety of techniques for stress reduction, peace of mind, stillness, and clarity.</p>

  <h2 class="band band--green side-title" style="top:442px">YOGA/PILATES</h2>
  <div class="thumb thumb--yoga section-mark" style="left:566px;top:426px" role="img" aria-label="Photo of a yoga pose on the beach"></div>
  <p class="abs side-text body-text" style="top:504px">Your highly qualified and experienced Yoga or Pilates instructor will come to you and create a fun and varied workout based on what you enjoy and what your goals are.</p>
</section>

</body>
</html>
```